Stationery Design Project for Nimbora, Chicago

Nimbora, a street parking application which helps car drivers find a street parking spot by offering an ideal path along which to look for parking. This path is calculated by our algorithm based on data (e.g. historical data, baseball games schedule, etc.). Along this path the driver will find a spot and will also save 70% of the search time. Customer we target is reg. between 21 and 45 yo.

We envision something young, fresh, bright and original. Slightly abstract maybe. It should represent the idea and elements of finding street parking in the city, e.g. car(s), parking spot, people, city, etc. (just ideas!).

Logo is attached.

Requirement:
- Business Cards (2 Sided Full Color CMYK)
- Letterhead (1 Sided Full Color CMYK)
- Envelope (1 Sided Full Color CMYK)
- Sticker (1 Sided Full Color CMYK), round with a 2inch diameter.

Reason: We're starting to get more and more designs and need more time to look into all of them. Very exciting!! Thanks to everybody!

Hi all, we're in the process of selecting our favs. Though choices!!! Really good submissions. Will keep you posted and sorry for the delay.

Target Market(s)

Car drivers and owners between 21 and 45

Industry/Entity Type

Parking

Requirements
Must have
• Sticker should be round and include company URL nimbora.com and the new logo which we will attach soon.
Should not have
• Should not be too serious or boring.

```html
<!DOCTYPE html>
<html lang="en">
<head>
<meta charset="UTF-8">
<title>Nimbora Business Card</title>
<link rel="stylesheet" href="https://fonts.googleapis.com/css2?family=Source+Sans+3:wght@400;600;700&display=swap">
<style>
  :root {
    --page: #e6e7e9;
    --card-white: #ffffff;
    --blue-deep: #2a3e9a;
    --blue-mid: #1f5fbf;
    --blue-bright: #1779cf;
    --ink: #111111;
    --swoosh-dark: #151515;
    --swoosh-grey: #5a5a5c;
    --white: #ffffff;
  }
  * { margin: 0; padding: 0; box-sizing: border-box; }
  html, body { width: 954px; height: 1200px; overflow: hidden; }
  body {
    background: var(--page);
    font-family: "Source Sans 3", sans-serif;
    position: relative;
  }
  .card {
    position: absolute;
    left: 74px;
    width: 796px;
    height: 454px;
    border-radius: 28px;
    overflow: hidden;
    box-shadow: 0 4px 10px rgba(0,0,0,0.18);
  }
  .card-front { top: 133px; background: var(--card-white); }
  .card-back {
    top: 650px;
    background: radial-gradient(ellipse 60% 75% at 50% 48%, var(--blue-bright) 0%, var(--blue-mid) 55%, var(--blue-deep) 100%);
  }
  .card-waves { position: absolute; inset: 0; }
  .brand {
    position: absolute;
    display: flex;
    align-items: center;
    gap: 24px;
  }
  .brand-dot {
    border-radius: 50%;
    background: var(--blue-mid);
    flex: none;
  }
  .brand-name {
    font-weight: 600;
    letter-spacing: 1px;
    line-height: 1;
  }
  .card-front .brand { left: 137px; top: 50px; }
  .card-front .brand-dot { width: 144px; height: 144px; }
  .card-front .brand-name { font-size: 104px; color: var(--ink); }
  .holder {
    position: absolute;
    right: 128px;
    top: 212px;
    font-size: 19px;
    font-weight: 700;
    color: var(--ink);
  }
  .holder-name { font-size: 25px; }
  .contact-list {
    position: absolute;
    left: 84px;
    top: 316px;
    list-style: none;
    color: var(--white);
    font-size: 19px;
    line-height: 32px;
  }
  .contact-list b { font-weight: 700; }
  .contact-divider {
    position: absolute;
    left: 312px;
    top: 330px;
    width: 1.5px;
    height: 108px;
    background: var(--white);
  }
  .address {
    position: absolute;
    left: 329px;
    top: 385px;
    color: var(--white);
    font-size: 19px;
    line-height: 27px;
  }
  .card-back .brand { left: 140px; top: 140px; }
  .card-back .brand-dot { width: 146px; height: 146px; background: var(--blue-deep); }
  .card-back .brand-name { font-size: 104px; color: var(--ink); }
  .back-contact {
    position: absolute;
    left: 0;
    right: 0;
    top: 336px;
    text-align: center;
    color: var(--white);
    font-size: 19px;
  }
  .back-contact b { font-weight: 700; }
</style>
</head>
<body>
  <section class="card card-front">
    <svg class="card-waves" viewBox="0 0 796 454" width="796" height="454" aria-hidden="true">
      <defs>
        <linearGradient id="frontBlue" x1="0" y1="0" x2="1" y2="0">
          <stop offset="0" stop-color="#2a3e9a"/>
          <stop offset="0.7" stop-color="#1779cf"/>
          <stop offset="1" stop-color="#2a3e9a"/>
        </linearGradient>
      </defs>
      <path d="M0,300 C110,260 230,245 360,268 C480,290 560,340 796,355 L796,454 L0,454 Z" fill="url(#frontBlue)"/>
      <path d="M0,268 C120,238 240,232 360,252 C470,272 560,318 796,328 L796,352 C560,338 480,288 360,266 C230,246 110,258 0,296 Z" fill="var(--swoosh-dark)"/>
      <path d="M0,282 C120,262 230,262 330,282 C240,274 120,278 0,300 Z" fill="var(--swoosh-grey)"/>
      <path d="M470,318 C560,340 680,345 796,338 L796,366 C690,372 580,362 470,318 Z" fill="var(--swoosh-grey)"/>
    </svg>
    <div class="brand">
      <span class="brand-dot"></span>
      <span class="brand-name">Nimbora</span>
    </div>
    <p class="holder"><span class="holder-name">Your Name</span> | Designation</p>
    <ul class="contact-list">
      <li><b>t</b> : 123-456-7890</li>
      <li><b>m</b> : 123-456-7890</li>
      <li><b>e</b> : name@nimbora.com</li>
      <li><b>w</b> : www.nimbora.com</li>
    </ul>
    <span class="contact-divider"></span>
    <p class="address">Street Name, City Name<br>State Name, Country Code</p>
  </section>

  <section class="card card-back">
    <div class="brand">
      <span class="brand-dot"></span>
      <span class="brand-name">Nimbora</span>
    </div>
    <p class="back-contact"><b>e</b> : name@nimbora.com | <b>w</b> : www.nimbora.com</p>
  </section>
</body>
</html>
```